Need a website setup for our new removalist business.
Our business is called Harbour Lane Removals and would like a website setup.
We don’t have a website, logo or design as of yet. Our truck is blue so something possibly that works and can incorporate the blue.

```html
<!DOCTYPE html>
<html lang="en">
<head>
<meta charset="utf-8">
<title>Harbour Lane Removals</title>
<link href="https://fonts.googleapis.com/css2?family=Poppins:wght@400;500;600;700;800&display=swap" rel="stylesheet">
<style>
:root{
  --blue:#0f4a7f;
  --blue-dark:#0c3d6b;
  --red:#b9122f;
  --ink:#121212;
  --muted:#666;
  --white:#fff;
  --black:#0e0e0e;
}
*{margin:0;padding:0;box-sizing:border-box}
html,body{width:1200px;height:3055px;overflow:hidden}
body{font-family:'Poppins',sans-serif;color:var(--ink);background:var(--white);position:relative}
.abs{position:absolute}
a{text-decoration:none;color:inherit}

.header{position:absolute;left:0;top:0;width:1200px;height:99px;background:var(--white)}
.brand{position:absolute;left:80px;top:26px;display:flex;align-items:center;gap:14px}
.brand-mark{width:40px;height:40px;background:var(--blue)}
.brand-name{font-weight:700;font-size:22px;line-height:24px;color:var(--ink);letter-spacing:.3px}
.brand-name small{display:block;font-size:13px;letter-spacing:4px;font-weight:700}
.nav a{position:absolute;top:40px;font-size:16px;color:#333}
.nav a.active{color:var(--red)}
.btn{position:absolute;display:flex;align-items:center;justify-content:center;font-weight:600;font-size:15px}
.btn-red{background:var(--red);color:var(--white)}
.btn-blue{background:var(--blue);color:var(--white)}
.btn-white{background:var(--white);color:var(--red)}

.hero-panel{left:0;top:99px;width:600px;height:507px;background:linear-gradient(160deg,#114f87,#0c3f70)}
.hero-photo{left:600px;top:99px;width:600px;height:507px;background:linear-gradient(160deg,#e9e3da,#cfa97a 60%,#a67848)}
.eyebrow{font-weight:600;font-size:20px;color:var(--red);text-transform:uppercase}
.hero-title{left:79px;top:212px;width:500px;font-weight:800;font-size:45px;line-height:62px;color:var(--white);letter-spacing:.5px}
.hero-text{left:79px;top:403px;width:440px;font-size:15.5px;line-height:29px;color:var(--white)}

.about-photo{left:111px;top:700px;width:446px;height:402px;background:linear-gradient(150deg,#d9d2c8,#c7a27a 55%,#a77c52);box-shadow:0 10px 30px rgba(0,0,0,.15)}
.section-title{font-weight:700;font-size:38px;color:var(--ink);line-height:46px}
.body-text{font-size:15.5px;line-height:32px;color:var(--muted)}

.stat{position:absolute;top:1186px;display:flex;align-items:center;gap:26px}
.stat svg{width:86px;height:86px}
.stat-num{font-weight:700;font-size:28px;line-height:34px}
.stat-label{font-size:14.5px;color:#444}

.card-photo{position:absolute;width:312px;height:254px}
.card{position:absolute;width:270px;height:139px;background:var(--white);box-shadow:0 8px 20px rgba(0,0,0,.08);padding:17px 10px 0 24px}
.card h3{font-weight:700;font-size:17px;line-height:24px;text-transform:uppercase;margin-bottom:4px;color:var(--ink);white-space:nowrap}
.card p{font-size:12px;line-height:24px;color:#777;white-space:nowrap}
.card a{display:block;margin-top:3px;font-size:12.5px;line-height:20px;font-weight:600;color:var(--red)}

.why-band{left:0;top:2359px;width:1200px;height:448px;background:var(--red)}
.why-photo{left:111px;top:2245px;width:489px;height:562px;background:linear-gradient(160deg,#9aa77e,#d9c3a0 45%,#b98a5a 75%,#566f8a)}

.footer{left:0;top:2807px;width:1200px;height:248px;background:var(--black);color:var(--white)}
.footer-brand{position:absolute;left:458px;top:42px;display:flex;align-items:center;gap:14px}
.footer-brand .brand-mark{background:var(--white)}
.footer-brand .brand-name{color:var(--white)}
.footer-nav a{position:absolute;top:125px;font-size:16px;font-weight:500;transform:translateX(-50%);white-space:nowrap}
.socials{position:absolute;left:543px;top:167px;display:flex;gap:6px}
.socials span{width:24px;height:24px;border-radius:50%;background:var(--white)}
.copyright{position:absolute;left:0;width:1200px;top:210px;text-align:center;font-size:12.5px}
</style>
</head>
<body>

<header class="header">
  <div class="brand"><div class="brand-mark"></div><div class="brand-name">HARBOUR LANE<small>REMOVALS</small></div></div>
  <nav class="nav">
    <a class="active" style="left:457px">Home</a>
    <a style="left:566px">About Us</a>
    <a style="left:696px">Our Services</a>
    <a style="left:854px">Reviews</a>
  </nav>
  <a class="btn btn-red" style="left:950px;top:30px;width:139px;height:42px;font-weight:500;font-size:16.5px">Contact Us</a>
</header>

<section>
  <div class="abs hero-panel"></div>
  <div class="abs hero-photo" role="img" aria-label="Family carrying moving boxes into a new home"></div>
  <p class="abs eyebrow" style="left:79px;top:178px">Making your move smooth &amp; simple</p>
  <h1 class="abs hero-title">PACK, MOVE, SETTLE WE’VE GOT YOU COVERED</h1>
  <p class="abs hero-text">Excepteur sint occaecat cupidatat non proident, sunt in culpa qui officia deserunt mollit anim</p>
  <a class="btn btn-white" style="left:79px;top:478px;width:131px;height:41px">Join With Us</a>
  <a class="btn btn-red" style="left:225px;top:478px;width:131px;height:41px">Get Started</a>
</section>

<section>
  <div class="abs about-photo" role="img" aria-label="Happy family playing with moving boxes"></div>
  <p class="abs eyebrow" style="left:615px;top:706px;font-size:24px;font-weight:700">About Us</p>
  <h2 class="abs section-title" style="left:615px;top:740px">WHO WE ARE</h2>
  <p class="abs body-text" style="left:615px;top:802px;width:490px">Sed ut perspiciatis unde omnis iste natus error sit voluptatem accusantium doloremque laudantium, totam rem aperiam, eaque ipsa quae ab illo inventore veritatis et quasi architecto beatae vitae dicta sunt explicabo.</p>
  <p class="abs body-text" style="left:615px;top:961px;width:480px">Nemo enim ipsam voluptatem quia voluptas sit aspernatur aut odit aut fugit, sed quia consequuntur.</p>
  <a class="btn btn-blue" style="left:615px;top:1047px;width:114px;height:43px">Read More</a>
</section>

<section>
  <div class="stat" style="left:111px">
    <svg viewBox="0 0 86 86"><polygon points="43,0 80,21 80,65 43,86 6,65 6,21" fill="var(--red)"/><circle cx="35" cy="36" r="6" fill="#fff"/><circle cx="51" cy="36" r="6" fill="#fff"/><rect x="26" y="45" width="34" height="14" rx="6" fill="#fff"/></svg>
    <div><div class="stat-num" style="color:var(--red)">100%</div><div class="stat-label">Customer Satisfaction</div></div>
  </div>
  <div class="stat" style="left:448px">
    <svg viewBox="0 0 86 86"><polygon points="43,0 80,21 80,65 43,86 6,65 6,21" fill="var(--blue)"/><rect x="27" y="29" width="32" height="28" fill="none" stroke="#fff" stroke-width="4"/><line x1="27" y1="38" x2="59" y2="38" stroke="#fff" stroke-width="3"/></svg>
    <div><div class="stat-num" style="color:var(--blue)">500+</div><div class="stat-label">Customer Moves</div></div>
  </div>
  <div class="stat" style="left:769px;top:1176px">
    <svg viewBox="0 0 86 86"><polygon points="43,0 80,21 80,65 43,86 6,65 6,21" fill="var(--black)"/><circle cx="43" cy="43" r="17" fill="#fff"/><polyline points="35,43 41,49 52,37" fill="none" stroke="var(--black)" stroke-width="4"/></svg>
    <div style="margin-top:-20px"><div class="stat-num">100%</div><div class="stat-label">Employee Background Checks</div></div>
  </div>
</section>

<section>
  <p class="abs eyebrow" style="left:0;width:1200px;text-align:center;top:1336px;font-size:24px;font-weight:700">Services</p>
  <h2 class="abs section-title" style="left:0;width:1200px;text-align:center;top:1372px">WHAT WE PROVIDE</h2>

  <div class="card-photo" style="left:111px;top:1448px;background:linear-gradient(150deg,#e6e2dc,#b88758)" role="img" aria-label="Movers packing boxes in a living room"></div>
  <div class="card-photo" style="left:444px;top:1448px;background:linear-gradient(150deg,#b57a3e,#f0c07a 60%,#d8a56c)" role="img" aria-label="Family walking among stacked boxes in a sunlit room"></div>
  <div class="card-photo" style="left:777px;top:1448px;background:linear-gradient(150deg,#eeeae4,#c9a478)" role="img" aria-label="Dog sitting beside moving boxes"></div>
  <div class="card" style="left:133px;top:1632px"><h3>Packing Services</h3><p>Excepteur sint occaecat cupidatat<br>non proident, sunt in culpa</p><a>View Details</a></div>
  <div class="card" style="left:466px;top:1632px"><h3>Storage Solutions</h3><p>Excepteur sint occaecat cupidatat<br>non proident, sunt in culpa</p><a>View Details</a></div>
  <div class="card" style="left:799px;top:1632px"><h3>Specialty Item Moving</h3><p>Excepteur sint occaecat cupidatat<br>non proident, sunt in culpa</p><a>View Details</a></div>

  <div class="card-photo" style="left:111px;top:1825px;background:linear-gradient(150deg,#ece8e2,#a9774a)" role="img" aria-label="Couple carrying a large box together"></div>
  <div class="card-photo" style="left:444px;top:1825px;background:linear-gradient(150deg,#eeece8,#cfac80)" role="img" aria-label="Stack of boxes next to a plant"></div>
  <div class="card-photo" style="left:777px;top:1825px;background:linear-gradient(150deg,#9a6a3c,#e1b987 60%,#c48a4c)" role="img" aria-label="Couple unpacking boxes on a sofa"></div>
  <div class="card" style="left:133px;top:2009px"><h3>Long-Distance Moving</h3><p>Excepteur sint occaecat cupidatat<br>non proident, sunt in culpa</p><a>View Details</a></div>
  <div class="card" style="left:466px;top:2009px"><h3>Local Moving</h3><p>Excepteur sint occaecat cupidatat<br>non proident, sunt in culpa</p><a>View Details</a></div>
  <div class="card" style="left:799px;top:2009px"><h3>Consultation</h3><p>Excepteur sint occaecat cupidatat<br>non proident, sunt in culpa</p><a>View Details</a></div>
</section>

<section>
  <div class="abs why-band"></div>
  <div class="abs why-photo" role="img" aria-label="Girl carrying a moving box outside a van"></div>
  <p class="abs" style="left:672px;top:2411px;font-weight:700;font-size:24px;color:var(--white)">WHY CHOOSE US</p>
  <h2 class="abs" style="left:671px;top:2450px;width:440px;font-weight:800;font-size:38px;line-height:46px;color:var(--white)">EXPERIENCE THE BEST MOVING</h2>
  <p class="abs body-text" style="left:672px;top:2558px;width:430px;color:var(--white)">Sed ut perspiciatis unde omnis iste natus error sit voluptatem accusantium doloremque laudantium, totam rem aperiam, eaque ipsa quae ab illo inventore veritatis et quasi architecto</p>
  <a class="btn btn-blue" style="left:672px;top:2704px;width:114px;height:43px">Read More</a>
</section>

<footer class="abs footer">
  <div class="footer-brand"><div class="brand-mark"></div><div class="brand-name">HARBOUR LANE<small>REMOVALS</small></div></div>
  <nav class="footer-nav">
    <a style="left:286px">HOME</a>
    <a style="left:415px">ABOUT US</a>
    <a style="left:578px">OUR SERVICES</a>
    <a style="left:734px">REVIEWS</a>
    <a style="left:886px">CONTACT US</a>
  </nav>
  <div class="socials"><span></span><span></span><span></span><span></span></div>
  <p class="copyright">(C) Copyright 2024 | All Rights Reserved</p>
</footer>

</body>
</html>
```